Harborview Estates Business Card for Apartment Buildings

Create business cards for resident managers who run apartment buildings. The audience is the public who are searching for apartment rentals, and current residents who live at the apartment building. Key design element will be incorporating the company logo, however, the logo cannot dominate. The building name and manager name are more important than the logo. Current business card design leaves little room for copy, so we may need to reduce the size on the current card to allow for more space for copy.

Target Market(s)

Adults 18-65 years of age, who are looking for an apartment rental, plus current residents who live at our apartment buildings.

Industry/Entity Type

Property Management

Contact Information for Business Card

A major design element will be use of the company logo. Important property and manager contact information must be part of the design. The size of the logo will need to be reduced to make room for building and manager contact copy.

Font styles to use
Sans Serif

Colors
3176b5
000000
959595
ffffff

Requirements
Must have
• 1) Incorporate the company logo.
• 2) Use the company colors (dark blue, black/grey, over white).
• 3) FEATURE THE BUILDING NAME
• 4) FEATURE THE MANAGER NAME
• 5) The company name is less important than BUILDING and MANAGER
• 6) Manager contact information
• **SEE ATTACHED CREATIVE BRIEF**
Nice to have
• 1) Back of card logo watermark
• 2) Ability to write notes on back of carfd
Should not have
• Avoid letting the company logo dominate the card, the building name and manager are more important than the company logo.

```html
<!DOCTYPE html>
<html lang="en">
<head>
<meta charset="utf-8">
<title>Harborview Estates Business Card</title>
<link href="https://fonts.googleapis.com/css2?family=Arimo:wght@400;700&display=swap" rel="stylesheet">
<style>
  :root {
    --brand-blue: #0f5a9a;
    --ink-black: #1d1d1f;
    --mark-grey: #959595;
    --paper: #ffffff;
    --stage: #3a3a3c;
    --faint: #ececee;
  }
  * { box-sizing: border-box; margin: 0; padding: 0; }
  html, body { width: 1200px; height: 880px; overflow: hidden; }
  body {
    background: var(--stage);
    font-family: "Arimo", Arial, sans-serif;
    position: relative;
  }
  .card {
    position: absolute;
    left: 280px;
    width: 640px;
    height: 366px;
    background: var(--paper);
    border-radius: 22px;
    overflow: hidden;
    box-shadow: 0 8px 22px rgba(0,0,0,0.45);
  }
  .card-back { top: 42px; }
  .card-front { top: 472px; }
  .watermark-circle {
    position: absolute;
    border: 14px solid var(--faint);
    border-radius: 50%;
  }
  .card-back .watermark-circle { width: 290px; height: 290px; left: 175px; top: 38px; }
  .card-front .watermark-circle { width: 230px; height: 230px; left: 400px; top: -20px; }
  .bands { position: absolute; left: 0; top: 0; width: 640px; height: 366px; }
  .company {
    position: absolute;
    left: 52px;
    top: 92px;
    display: flex;
    align-items: center;
    gap: 12px;
  }
  .company-dot {
    width: 44px; height: 44px;
    border-radius: 50%;
    background: var(--brand-blue);
  }
  .company-name {
    color: var(--brand-blue);
    font-weight: 700;
    font-size: 24px;
    line-height: 1.05;
    letter-spacing: 0.5px;
  }
  .manager {
    position: absolute;
    left: 52px;
    top: 246px;
    color: var(--paper);
  }
  .manager-name { font-weight: 700; font-size: 18px; letter-spacing: 0.3px; }
  .manager-title { font-size: 14px; margin-top: 2px; }
  .contact-list {
    position: absolute;
    left: 52px;
    top: 298px;
    list-style: none;
    color: var(--paper);
    font-size: 13px;
    line-height: 19px;
  }
  .contact-list li { display: flex; align-items: center; gap: 8px; }
  .contact-list svg { width: 12px; height: 12px; fill: var(--paper); }
  .address {
    position: absolute;
    right: 36px;
    top: 246px;
    color: var(--paper);
    font-size: 13px;
    line-height: 19px;
    text-align: right;
    font-style: normal;
  }
</style>
</head>
<body>

<section class="card card-back" aria-label="Card back">
  <div class="watermark-circle"></div>
</section>

<section class="card card-front" aria-label="Card front">
  <div class="watermark-circle"></div>

  <svg class="bands" viewBox="0 0 640 366" aria-hidden="true">
    <path fill="var(--ink-black)" d="M0 236 H330 Q346 236 348 220 Q350 200 372 200 H640 V366 H0 Z"/>
    <path fill="var(--brand-blue)" d="M0 290 H336 Q354 290 356 272 Q358 218 380 218 H640 V366 H0 Z"/>
  </svg>

  <div class="company">
    <span class="company-dot"></span>
    <span class="company-name">HARBORVIEW<br>ESTATES LLC</span>
  </div>

  <div class="manager">
    <p class="manager-name">DANIEL HARTWELL</p>
    <p class="manager-title">Property Manager</p>
  </div>

  <ul class="contact-list">
    <li><svg viewBox="0 0 12 12"><path d="M2 1h3l1 3-1.5 1a7 7 0 0 0 2.5 2.5L8 6l3 1v3a1 1 0 0 1-1 1A9 9 0 0 1 1 2a1 1 0 0 1 1-1z"/></svg>207-555-0148</li>
    <li><svg viewBox="0 0 12 12"><path d="M3 1h6v3H3zM1 5h10v5H9v-2H3v2H1zM3 9h6v2H3z"/></svg>207-555-0193</li>
    <li><svg viewBox="0 0 12 12"><path d="M1 3h10v7H1zM1.5 3.5 6 7l4.5-3.5" stroke="var(--brand-blue)" stroke-width="1"/></svg>daniel@harborviewestates.us</li>
  </ul>

  <address class="address">
    1520 Seabright Avenue #B210<br>
    Portland, ME 04101<br>
    www.harborviewestates.us
  </address>
</section>

</body>
</html>
```